Boutique custom software development company needs new business card

Our nearly 20 year old custom software development company would like to better include the fact that we are now providing Bitcoin services. These new services are B2B include education (how to acquire and securely hold Bitcoin) and integrating Bitcoin payments into existing ecommerce sites or other existing systems. Please keep the card clean and simple. Attached is our current design and some other files. vextorial.com

Target Market(s)

businesses owners interested in long term relationship

Industry/Entity Type

Custom software development and Bitcoin

Contact Information for Business Card

Dale Parker, dale@vextorial.com, vextorial.com, (888) 555-VXTRL

Font styles to use
Other font styles liked:
• monospace

Requirements
Must have
• double-sided
Nice to have
• clean and simple
Should not have
• physical address

```html
<!DOCTYPE html>
<html lang="en">
<head>
<meta charset="utf-8">
<title>Vextorial business card</title>
<link rel="stylesheet" href="https://fonts.googleapis.com/css2?family=Montserrat:wght@400;500;700;800&display=swap">
<style>
  :root {
    --brand-blue: #3f73b9;
    --brand-orange: #f07c22;
    --card-white: #ffffff;
    --backdrop: #c4c4c4;
    --card-shadow: rgba(0, 0, 0, 0.22);
  }
  * { box-sizing: border-box; margin: 0; padding: 0; }
  html, body { width: 1200px; height: 800px; overflow: hidden; }
  body {
    background: var(--backdrop);
    font-family: "Montserrat", sans-serif;
    display: flex;
    align-items: center;
    justify-content: center;
    gap: 40px;
  }
  .card {
    position: relative;
    width: 560px;
    height: 320px;
    background: var(--card-white);
    border-radius: 16px;
    overflow: hidden;
    box-shadow: 0 10px 28px var(--card-shadow);
  }

  /* Shared wordmark */
  .wordmark__name {
    font-weight: 800;
    letter-spacing: 1px;
    line-height: 1;
    color: var(--brand-blue);
  }
  .wordmark__tagline {
    font-weight: 500;
    color: var(--brand-blue);
    line-height: 1.25;
  }
  .wordmark__services {
    font-weight: 500;
    color: var(--brand-orange);
    line-height: 1.25;
  }

  /* Front side */
  .card--front .wordmark {
    position: absolute;
    top: 30px;
    right: 56px;
  }
  .card--front .wordmark__name { font-size: 40px; }
  .card--front .wordmark__tagline { font-size: 13.5px; margin-top: 5px; }
  .card--front .wordmark__services { font-size: 12px; margin-top: 2px; }

  .accent-orange {
    position: absolute;
    left: 482px; top: 118px;
    width: 78px; height: 84px;
    background: var(--brand-orange);
  }
  .accent-blue {
    position: absolute;
    left: 372px; top: 146px;
    width: 100px; height: 100px;
    background: var(--brand-blue);
  }
  .holder-name {
    position: absolute;
    left: 40px; top: 176px;
    font-weight: 800;
    font-size: 22px;
    line-height: 1.2;
    letter-spacing: 1px;
    text-transform: uppercase;
  }
  .holder-name__first { color: var(--brand-orange); }
  .holder-name__last { color: var(--brand-blue); }
  .contact-band {
    position: absolute;
    left: 0; top: 214px;
    width: 362px; height: 84px;
    background: var(--brand-blue);
    padding: 10px 0 0 40px;
  }
  .contact-list { list-style: none; }
  .contact-list__item {
    display: flex;
    align-items: center;
    gap: 10px;
    color: var(--card-white);
    font-size: 14px;
    font-weight: 500;
    height: 21px;
    letter-spacing: 0.3px;
  }
  .contact-icon {
    width: 17px; height: 17px;
    background: var(--card-white);
    border-radius: 3px;
    display: flex; align-items: center; justify-content: center;
    flex: none;
  }

  /* Back side */
  .card--back {
    display: flex;
    align-items: center;
    justify-content: center;
  }
  .card--back .wordmark__name { font-size: 58px; }
  .card--back .wordmark__tagline { font-size: 20px; margin-top: 8px; }
  .card--back .wordmark__services { font-size: 16px; margin-top: 6px; }
</style>
</head>
<body>
  <section class="card card--front" aria-label="Business card front">
    <div class="wordmark">
      <div class="wordmark__name">VEXTORIAL</div>
      <div class="wordmark__tagline">developer of custom applications</div>
      <div class="wordmark__services">Bitcoin education &amp; payment integration</div>
    </div>
    <div class="accent-orange"></div>
    <div class="accent-blue"></div>
    <h1 class="holder-name"><span class="holder-name__first">Dale</span> <span class="holder-name__last">Parker</span></h1>
    <div class="contact-band">
      <ul class="contact-list">
        <li class="contact-list__item">
          <span class="contact-icon">
            <svg width="11" height="11" viewBox="0 0 24 24" aria-hidden="true"><path fill="var(--brand-orange)" d="M6.6 10.8a15 15 0 0 0 6.6 6.6l2.2-2.2c.3-.3.7-.4 1-.2 1.1.4 2.3.6 3.6.6.6 0 1 .4 1 1V20c0 .6-.4 1-1 1A17 17 0 0 1 3 4c0-.6.4-1 1-1h3.5c.6 0 1 .4 1 1 0 1.3.2 2.5.6 3.6.1.3 0 .7-.2 1z"/></svg>
          </span>
          (888) 555-VXTRL
        </li>
        <li class="contact-list__item">
          <span class="contact-icon">
            <svg width="11" height="11" viewBox="0 0 24 24" aria-hidden="true"><rect x="2" y="5" width="20" height="14" rx="1" fill="var(--brand-orange)"/><path d="M2 6l10 7 10-7" fill="none" stroke="#fff" stroke-width="2"/></svg>
          </span>
          dale@vextorial.com
        </li>
        <li class="contact-list__item">
          <span class="contact-icon">
            <svg width="11" height="11" viewBox="0 0 24 24" aria-hidden="true"><circle cx="12" cy="12" r="10" fill="var(--brand-orange)"/><path d="M2 12h20M12 2c3 3 3 17 0 20M12 2c-3 3-3 17 0 20" fill="none" stroke="#fff" stroke-width="1.5"/></svg>
          </span>
          www.vextorial.com
        </li>
      </ul>
    </div>
  </section>

  <section class="card card--back" aria-label="Business card back">
    <div class="wordmark">
      <div class="wordmark__name">VEXTORIAL</div>
      <div class="wordmark__tagline">developer of custom applications</div>
      <div class="wordmark__services">Bitcoin education &amp; payment integration</div>
    </div>
  </section>
</body>
</html>
```